Veranix - Solution provider in business consulting

Veranix is a swiss based company providing solutions for developing markets. The business covers various fields of business consulting, such as supply chain, product costs, quality management and manufacturing management. The Business operates in a efficient, straight and solution oriented manner.
The final design should communicate these characteristics. Asian people as well as as western people shall identify the qualities of the company at first sight.
The customer needs business cards with a simple view but an recognizable design, printed in high quality. Engraved elements such as the globe or simple words are possible.
Available colors are: (RAL)
102/102/102
51/102/102
153/204/153
255/102/51
Font: Calibri

```html
<!DOCTYPE html>
<html lang="en">
<head>
<meta charset="utf-8">
<title>Veranix – Business Card</title>
<link href="https://fonts.googleapis.com/css2?family=Carlito:wght@400;700&display=swap" rel="stylesheet">
<style>
  :root {
    --backdrop: #e4e2dd;
    --card-black: #0a0a0a;
    --card-white: #fafafa;
    --ink-dark: #1a1a1a;
    --ink-light: #ffffff;
  }
  * { box-sizing: border-box; margin: 0; padding: 0; }
  html, body {
    width: 1200px;
    height: 1022px;
    overflow: hidden;
  }
  body {
    background: var(--backdrop);
    font-family: "Carlito", "Calibri", sans-serif;
    display: flex;
    align-items: center;
    justify-content: center;
    gap: 40px;
  }
  .card {
    position: relative;
    width: 540px;
    height: 340px;
    border-radius: 18px;
    overflow: hidden;
    background: var(--card-black);
    box-shadow: 0 8px 24px rgba(0,0,0,0.25);
  }

  /* Front side */
  .globe-area {
    position: absolute;
    left: -90px;
    top: 40px;
    width: 470px;
    height: 470px;
    border-radius: 50%;
    background: radial-gradient(circle at 45% 40%, #ffffff 0%, var(--card-white) 70%, #ececec 100%);
  }
  .contact {
    position: absolute;
    left: 34px;
    top: 150px;
    color: var(--ink-dark);
  }
  .contact-name {
    font-weight: 700;
    font-size: 25px;
    line-height: 1;
  }
  .contact-role {
    font-size: 14px;
    margin-top: 4px;
    margin-bottom: 12px;
  }
  .contact-address {
    font-size: 14px;
    line-height: 1.25;
    margin-bottom: 6px;
  }
  .contact-list { list-style: none; }
  .contact-list li {
    display: flex;
    align-items: center;
    gap: 9px;
    font-size: 14px;
    line-height: 1.3;
  }
  .contact-list svg {
    width: 11px;
    height: 11px;
    flex: none;
  }

  /* Back side */
  .brand {
    position: absolute;
    inset: 0;
    display: flex;
    align-items: center;
    justify-content: center;
    gap: 14px;
    color: var(--ink-light);
  }
  .brand-dot {
    width: 46px;
    height: 46px;
    border-radius: 50%;
    background: var(--ink-light);
  }
  .brand-name {
    font-size: 58px;
    font-weight: 400;
    letter-spacing: 1px;
  }
</style>
</head>
<body>

  <section class="card card-front" aria-label="Business card front">
    <div class="globe-area" role="img" aria-label="Large white globe illustration with dark continents"></div>
    <div class="contact">
      <p class="contact-name">Marco Lenz</p>
      <p class="contact-role">CEO</p>
      <p class="contact-address">Veranix GmbH Talweg 14<br>9246 Niederwil Switzerland</p>
      <ul class="contact-list">
        <li>
          <svg viewBox="0 0 12 12" aria-hidden="true"><rect x="3" y="0.5" width="6" height="11" rx="1" fill="none" stroke="#1a1a1a"/><line x1="5" y1="10" x2="7" y2="10" stroke="#1a1a1a"/></svg>
          +41 79 555 0142
        </li>
        <li>
          <svg viewBox="0 0 12 12" aria-hidden="true"><path d="M2 1 L4.5 1 L5.5 3.5 L4 4.8 C4.8 6.6 5.4 7.2 7.2 8 L8.5 6.5 L11 7.5 L11 10 C6 11 1 6 2 1 Z" fill="#1a1a1a"/></svg>
          +41 71 555 0187
        </li>
        <li>
          <svg viewBox="0 0 12 12" aria-hidden="true"><rect x="0.5" y="2" width="11" height="8" fill="none" stroke="#1a1a1a"/><polyline points="0.5,2 6,7 11.5,2" fill="none" stroke="#1a1a1a"/></svg>
          marco.lenz@veranix.ch
        </li>
        <li>
          <svg viewBox="0 0 12 12" aria-hidden="true"><circle cx="6" cy="6" r="5.5" fill="#1a1a1a"/><ellipse cx="6" cy="6" rx="2.4" ry="5.5" fill="none" stroke="#fafafa" stroke-width="0.8"/><line x1="0.5" y1="6" x2="11.5" y2="6" stroke="#fafafa" stroke-width="0.8"/></svg>
          www.veranix.ch
        </li>
      </ul>
    </div>
  </section>

  <section class="card card-back" aria-label="Business card back">
    <div class="brand">
      <span class="brand-dot" aria-hidden="true"></span>
      <span class="brand-name">Veranix</span>
    </div>
  </section>

</body>
</html>
```